Redesign current business card for food company

i would like to redesign my business card. our company is food company, our product range from chips, juices, milk and etc (mostly dried food stuff).
I want o keep same logo but , the rest is open to new design.
you can check at our website about our company www.orvelpantry.com

Target Market(s)

most of food company

Industry/Entity Type

Business

Contact Information for Business Card

I want to keep more to blue color...

Colors
3176b5
abd036

Requirements
Must have
• our old logo
Nice to have
• we do not mind to have nice material on bus card in order to accomplish nice design. for example: using spot uv, embossed and etc.

```html
<!DOCTYPE html>
<html lang="en">
<head>
<meta charset="utf-8">
<title>Orvel Business Card</title>
<link href="https://fonts.googleapis.com/css2?family=Open+Sans:wght@400;600&display=swap" rel="stylesheet">
<style>
  :root {
    --stage: #eceef1;
    --card-white: #ffffff;
    --brand-blue: #1a9be6;
    --deep-blue: #1f7fd0;
    --sky-blue: #19c3fb;
    --ink-grey: #4d5258;
  }
  * { margin: 0; padding: 0; box-sizing: border-box; }
  html, body { width: 1200px; height: 900px; overflow: hidden; }
  body {
    background: var(--stage);
    font-family: "Open Sans", sans-serif;
    position: relative;
  }
  .card {
    position: absolute;
    width: 555px;
    height: 343px;
    overflow: hidden;
    box-shadow: 0 6px 18px rgba(0,0,0,0.18);
  }
  .card-front { left: 238px; top: 62px; background: var(--card-white); }
  .card-back {
    left: 457px; top: 518px; width: 560px;
    background: linear-gradient(180deg, var(--sky-blue) 0%, var(--deep-blue) 100%);
  }
  .back-curve { position: absolute; inset: 0; }
  .company-wordmark {
    position: absolute;
    font-weight: 600;
    line-height: 1;
  }
  .card-front .company-wordmark { left: 44px; top: 132px; font-size: 72px; color: var(--brand-blue); }
  .card-back .company-wordmark { left: 118px; top: 102px; font-size: 112px; color: #ffffff; }
  .contact { position: absolute; left: 292px; top: 44px; color: var(--ink-grey); }
  .person-name { font-size: 20px; font-weight: 600; color: var(--brand-blue); line-height: 26px; }
  .person-title { font-size: 15px; line-height: 20px; }
  .company-name { margin-top: 18px; font-size: 17px; font-weight: 600; color: var(--brand-blue); line-height: 22px; }
  .address { font-size: 15px; line-height: 23px; }
  .contact-list { list-style: none; margin-top: 15px; }
  .contact-list li { display: flex; align-items: center; font-size: 15px; line-height: 23px; }
  .contact-list svg { width: 12px; height: 12px; margin-right: 9px; fill: var(--brand-blue); flex: none; }
</style>
</head>
<body>
  <section class="card card-front">
    <div class="company-wordmark">orvel</div>
    <div class="contact">
      <p class="person-name">Daniel Hartono</p>
      <p class="person-title">President</p>
      <p class="company-name">Orvel Enterprises Corp.</p>
      <p class="address">2481 W 5th St.Ontario<br>CA 91762</p>
      <ul class="contact-list">
        <li><svg viewBox="0 0 12 12"><path d="M2.5 1l2 2.2-1 1.3c.7 1.5 1.8 2.6 3.3 3.3l1.3-1 2.2 2-1 1.7C5.5 10.3 1.7 6.5 1 2z"/></svg>909 555 0142</li>
        <li><svg viewBox="0 0 12 12"><path d="M3 1h5v3H3zM1 5h10v6H1zm2 2v1h2V7zm4 0v3h2V7z"/></svg>909 555 0143</li>
        <li><svg viewBox="0 0 12 12"><path d="M3 0h6a1 1 0 011 1v10a1 1 0 01-1 1H3a1 1 0 01-1-1V1a1 1 0 011-1zm0 2v7h6V2z"/></svg>626 555 0178</li>
        <li><svg viewBox="0 0 12 12"><path d="M0 2h12v1L6 7 0 3zm0 2.5l6 4 6-4V10H0z"/></svg>Daniel@orvelpantry.com</li>
        <li><svg viewBox="0 0 12 12"><path d="M6 0a6 6 0 100 12A6 6 0 006 0zm-1 2.5c1 .3 1.5 1 1 2-.6.8-2 .6-2 2 0 1 1 1.3 1 2.5-1.6-.3-3-1.8-3-3.5 0-1.4.9-2.6 3-3zm3.5 1.3C9.5 4.5 10 5.5 10 6.5c-.8.2-1.5-.4-2-1 .1-.7.3-1.2.5-1.7z"/></svg>www.orvelpantry.com</li>
      </ul>
    </div>
  </section>

  <section class="card card-back">
    <svg class="back-curve" viewBox="0 0 560 343" preserveAspectRatio="none" aria-hidden="true">
      <path d="M0 215 C180 210 330 120 375 0 L560 0 L560 343 L0 343 Z" fill="#1f86d8" opacity="0.55"/>
    </svg>
    <div class="company-wordmark">orvel</div>
  </section>
</body>
</html>
```